New Business Card for our Indoor Golf Training Facility

We are looking for designs for a new business card for our indoor golf training facility. Attached is our logo, our logo with our slogan, and here is our elevator pitch (What makes us different from the others) not sure if all the info will fit on one card, maybe you can condense the elevator pitch? here is the info

Elevator Pitch
We work with serious golfers and those that want to be serious golfers…
to make you better, faster, at all phases of the game…
We use the same state-of-the-art technology as professional golfers…
which produces data sets that shows your improvement in real time.
Our facility is available 24/7 to our members, which allows you to improve on your time.

our website: www.birchpinlinks.com

Target Market(s)

Golfers

Font styles to use
Serif
Sans Serif

Colors
ec1f27
f59195
fbd4d5
919191
d3d3d3
1b1b1b

Requirements
Must have
• our logo or our logo with the slogan, elevator pitch (can be condensed or shortened)

```html
<!DOCTYPE html>
<html lang="en">
<head>
<meta charset="utf-8">
<title>Birch Pin Links – Business Card</title>
<link href="https://fonts.googleapis.com/css2?family=Open+Sans:wght@400;600;700&display=swap" rel="stylesheet">
<style>
  :root {
    --backdrop: #9a9a9a;
    --card-dark: #2a292a;
    --brand-red: #ec3d35;
    --text-light: #e6e6e6;
    --white: #ffffff;
    --rule: #4a494a;
  }
  * { margin: 0; padding: 0; box-sizing: border-box; }
  html, body { width: 1200px; height: 900px; overflow: hidden; }
  body {
    background: var(--backdrop);
    font-family: "Open Sans", Arial, sans-serif;
    position: relative;
  }
  .card {
    position: absolute;
    width: 478px;
    height: 296px;
    overflow: hidden;
    box-shadow: 2px 4px 8px rgba(0,0,0,0.35);
  }
  .card-front {
    left: 120px; top: 275px;
    background: var(--card-dark);
    border-radius: 0 56px 0 56px;
  }
  .card-back {
    left: 606px; top: 274px;
    height: 294px;
    background: var(--card-dark);
    border-radius: 56px 0 56px 0;
  }

  /* Front */
  .brand-name {
    position: absolute;
    right: 32px; top: 84px;
    color: var(--brand-red);
    font-weight: 700;
    font-size: 33px;
    letter-spacing: -0.3px;
    line-height: 1;
    white-space: nowrap;
  }
  .tagline {
    position: absolute;
    right: 32px; top: 122px;
    color: var(--brand-red);
    font-size: 12px;
    white-space: nowrap;
  }
  .person-name {
    position: absolute;
    left: 25px; top: 181px;
    color: var(--brand-red);
    font-weight: 600;
    font-size: 17px;
  }
  .person-title {
    position: absolute;
    left: 25px; top: 200px;
    color: var(--text-light);
    font-size: 14px;
  }
  .title-rule {
    position: absolute;
    left: 213px; top: 210px;
    width: 237px; height: 1px;
    background: var(--rule);
  }
  .contact-list {
    position: absolute;
    left: 25px; top: 229px;
    list-style: none;
    color: var(--text-light);
    font-size: 14px;
    line-height: 18px;
  }
  .contact-list li { display: flex; align-items: center; gap: 3px; }
  .contact-list svg { width: 15px; height: 15px; }
  .address {
    position: absolute;
    right: 28px; top: 229px;
    color: var(--text-light);
    font-size: 14px;
    line-height: 18px;
    text-align: right;
    font-style: normal;
  }

  /* Back */
  .pitch-panel {
    position: absolute;
    left: 0; top: 0;
    width: 100%; height: 236px;
    background: var(--brand-red);
    color: var(--white);
    font-size: 13px;
    line-height: 17px;
    text-align: center;
    padding-top: 91px;
  }
  .pitch-panel p { margin-bottom: 6px; }
  .visit-line {
    position: absolute;
    left: 0; top: 254px;
    width: 100%;
    text-align: center;
    color: var(--white);
    font-size: 13px;
  }
  .visit-line .site { color: var(--brand-red); }
</style>
</head>
<body>
  <section class="card card-front">
    <div class="brand-name">Birch Pin Links</div>
    <div class="tagline">Par Is Good. Under Is Better. Be Better.</div>

    <h1 class="person-name">Daniel Marsh</h1>
    <div class="person-title">Head Director of Instruction</div>
    <div class="title-rule"></div>

    <ul class="contact-list">
      <li>
        <svg viewBox="0 0 16 16" aria-hidden="true">
          <circle cx="8" cy="8" r="6.5" fill="none" stroke="#ec3d35" stroke-width="1.3"/>
          <path d="M6 4.5 L7 6.6 L6.3 7.3 Q7 9 8.7 9.7 L9.4 9 L11.5 10 L11 11.3 Q7 11.5 4.7 5 Z" fill="#ec3d35"/>
        </svg>
        555-210-3388
      </li>
      <li>
        <svg viewBox="0 0 16 16" aria-hidden="true">
          <circle cx="8" cy="8" r="6.5" fill="#ec3d35"/>
          <circle cx="8" cy="8" r="3.3" fill="none" stroke="#2a292a" stroke-width="1.3"/>
          <path d="M4.7 8 H11.3 M8 4.7 V11.3" stroke="#2a292a" stroke-width="1"/>
        </svg>
        www.birchpinlinks.com
      </li>
    </ul>

    <address class="address">
      1840 W. Alder Rd. Unit B4<br>
      Fairview, OH 45000
    </address>
  </section>

  <section class="card card-back">
    <div class="pitch-panel">
      <p>We work with serious golfers and those that want to be serious golfers…<br>to make you better, faster, at all phases of the game…</p>
      <p>We use the same state-of-the-art technology as professional golfers…<br>which produces data sets that shows your improvement in real time.</p>
      <p>Our facility is available 24/7 to our members, which allows<br>you to improve on your time.</p>
    </div>
    <div class="visit-line">Visit <span class="site">www.birchpinlinks.com</span> for more details.</div>
  </section>
</body>
</html>
```